My Pebble Porch Path Blog Re-Do Launch

I need a blog makeover. Someone started for me and they sold their company. The blog is primarily spiritual/inspirational. I would eventually like to monetize and launch some ebooks and/or other products. I am open to suggestions. I am learning as we go along, so please keep that in mind. The final design should be warm and welcoming. I am open to suggestions. I am looking to build a relationship.

Target Market(s)

women, moms, females with chronic health issues, moms of special needs kids, those who need encouragement

Industry/Entity Type

Religious

Number of Pages Required

4 page

Font styles to use
Sans Serif

Colors
eddcec
fdf9cf
ffffff

Requirements
Must have
• I would like my main page to have a short about section, relevant posts, recent posts, and archive posts. The main page should also have a place to subscribe as well a search feature.
Nice to have
• Buttons (grab my button), blogs I follow, e-cart capabilities

```html
<!DOCTYPE html>
<html lang="en">
<head>
<meta charset="utf-8">
<title>My Pebble Porch Path</title>
<link href="https://fonts.googleapis.com/css2?family=Abel&family=Open+Sans:wght@400;600&family=Raleway:wght@400;500&display=swap" rel="stylesheet">
<style>
:root{
  --ink:#2b2b2b;
  --night:#000000;
  --white:#ffffff;
  --cream:#f6f1dc;
  --blush:#eddcec;
  --blush-deep:#5e4a5c;
  --line:#e4e4e4;
  --bar:#ebebeb;
  --bar-icon:#b9b9b9;
  --text:#555555;
  --muted:#a9a9a9;
  --heading:#4a4a4a;
  --tile:#f4f4f4;
}
*{margin:0;padding:0;box-sizing:border-box}
html,body{width:1200px;height:2521px;overflow:hidden;background:var(--white)}
body{position:relative;font-family:"Open Sans",Arial,sans-serif;color:var(--text)}
.abs{position:absolute}
svg.icon{width:14px;height:14px;vertical-align:-2px;fill:none;stroke:currentColor;stroke-width:1.6}

/* header */
.site-header{left:0;top:0;width:1200px;height:72px;background:var(--ink)}
.brand{left:97px;top:8px;display:flex;align-items:center;gap:24px}
.brand-mark{width:82px;height:82px;background:var(--blush);margin-top:44px}
.brand-name{font-family:"Raleway",sans-serif;font-size:21px;color:var(--white);margin-top:-44px}
.main-nav{left:650px;top:28px;display:flex;font-family:"Raleway",sans-serif;font-size:12px;color:#9a9a9a;letter-spacing:.3px}
.main-nav span{padding:0 22px;border-right:1px solid #666;line-height:14px}
.main-nav span.active{color:var(--white)}
.main-nav .search{border:none;padding-left:22px;color:#bbb}

/* hero */
.hero{left:0;top:72px;width:1200px;height:514px;background:linear-gradient(180deg,#5b4634 0%,#a27a47 35%,#d29a4c 55%,#8c6238 75%,#2a1d14 100%)}
.hero-title{left:140px;top:274px;font-family:"Raleway",sans-serif;font-size:50px;font-weight:500;color:var(--white);text-shadow:0 2px 6px rgba(0,0,0,.35)}
.hero-arrow{top:286px;width:30px;height:46px;stroke:var(--white);stroke-width:2;fill:none}

/* panels */
.panel{border:1px solid var(--line);background:var(--white);box-shadow:0 1px 3px rgba(0,0,0,.06)}
.panel-head{height:58px;border-bottom:1px solid var(--line);display:flex;align-items:center;justify-content:space-between;padding:0 26px 0 28px}
.panel-title{font-family:"Abel",sans-serif;font-size:25px;color:var(--heading)}
.pager{display:flex;gap:5px}
.pager i{width:19px;height:19px;border-radius:50%;background:#c4c4c4;display:block;position:relative}
.pager i::after{content:"";position:absolute;top:6px;left:7px;width:5px;height:5px;border-left:2px solid var(--white);border-bottom:2px solid var(--white);transform:rotate(45deg)}
.pager i.next::after{left:5px;transform:rotate(-135deg)}
.photo{display:block}
.meta{font-family:"Abel",sans-serif;font-size:11px;color:var(--muted);display:flex;gap:30px}
.meta span{display:flex;gap:6px;align-items:center}
.share-bar{position:absolute;left:0;bottom:0;width:100%;height:40px;background:var(--bar);display:flex}
.share-bar span{flex:0 0 107px;display:flex;align-items:center;justify-content:center;border-right:1px solid #f7f7f7;color:var(--bar-icon)}
.share-bar span i{width:13px;height:13px;border-radius:50%;background:var(--bar-icon);display:block}
.share-bar .read{flex:1;border:none;font-family:"Abel",sans-serif;font-size:16px;color:#c3c3c3}

.post-name{font-family:"Abel",sans-serif;font-size:17px;color:#333}
.body-copy{font-size:12px;line-height:21px;color:var(--text)}

/* archive */
.arch-item{left:326px;width:304px;height:87px;background:var(--tile);display:flex}
.arch-item .thumb{width:126px;height:87px;flex:none}
.arch-item .txt{padding:8px 12px;font-family:"Abel",sans-serif;font-size:11px;line-height:15px;color:#444}
.arch-item .meta{margin-top:6px;font-size:10px}

/* sidebar */
.input{height:37px;border:1px solid var(--line);background:#f7f7f7;font-size:11px;color:#aaa;padding:10px 14px}
.btn-dark{height:35px;background:var(--ink);color:var(--white);font-size:14px;display:flex;align-items:center;justify-content:center}
.recent{display:flex;gap:14px;padding:0 0 14px;margin-bottom:14px;border-bottom:1px solid var(--line)}
.recent:last-child{border:none}
.recent .thumb{width:84px;height:84px;flex:none}
.recent .who{font-family:"Abel",sans-serif;font-size:15px;color:#333}
.recent .meta{font-size:11px;gap:14px;margin:4px 0 2px}
.recent .blurb{font-family:"Abel",sans-serif;font-size:11px;line-height:19px;color:var(--muted)}

/* about band */
.about-band{left:0;top:1786px;width:1200px;height:483px;background:var(--cream)}
.about-title{left:101px;top:1896px;font-family:"Abel",sans-serif;font-size:24px;color:var(--heading)}
.about-copy{left:99px;top:1948px;width:566px;font-size:12.5px;line-height:21px;color:#444}
.about-copy p+p{margin-top:21px}
.cart-btn{left:99px;top:2155px;width:148px;height:45px;border-radius:23px;background:var(--blush);font-family:"Abel",sans-serif;font-size:21px;color:var(--blush-deep);display:flex;align-items:center;justify-content:center;gap:14px;box-shadow:0 2px 3px rgba(0,0,0,.12)}

/* footer */
.site-footer{left:0;top:2269px;width:1200px;height:252px;background:var(--night)}
.social{left:0;top:2316px;width:1200px;display:flex;justify-content:center;gap:25px}
.social i{width:45px;height:45px;border:2px solid var(--white);border-radius:50%;display:block}
.foot-nav{left:0;top:2398px;width:1200px;display:flex;justify-content:center;font-family:"Raleway",sans-serif;font-size:11px;color:#bbb}
.foot-nav span{padding:0 31px;border-right:1px solid #777;line-height:13px}
.foot-nav span:last-child{border:none}
.foot-nav .active{color:var(--white)}
.copyright{left:0;top:2445px;width:1200px;text-align:center;font-family:"Raleway",sans-serif;font-size:13px;color:var(--white)}
</style>
</head>
<body>

<svg width="0" height="0" style="position:absolute">
  <symbol id="i-cal" viewBox="0 0 14 14"><rect x="1.5" y="2.5" width="11" height="10"/><path d="M1.5 5.5h11M4.5 1v3M9.5 1v3"/></symbol>
  <symbol id="i-pen" viewBox="0 0 14 14"><path d="M2 12l1-3 7-7 2 2-7 7z"/></symbol>
  <symbol id="i-chat" viewBox="0 0 14 14"><path d="M1.5 3h11v6h-6l-3 3v-3h-2z"/></symbol>
  <symbol id="i-clock" viewBox="0 0 14 14"><circle cx="7" cy="7" r="5.5"/><path d="M7 4v3.3l2 1.4"/></symbol>
  <symbol id="i-mail" viewBox="0 0 14 14"><rect x="1.5" y="3" width="11" height="8"/><path d="M1.5 3l5.5 4.5L12.5 3"/></symbol>
  <symbol id="i-cart" viewBox="0 0 14 14"><path d="M1 2h2l1.6 7h6.4l1.5-5H4" /><circle cx="5.5" cy="11.8" r="1"/><circle cx="10" cy="11.8" r="1"/></symbol>
  <symbol id="i-search" viewBox="0 0 14 14"><circle cx="6" cy="6" r="4"/><path d="M9 9l3.5 3.5"/></symbol>
</svg>

<header class="site-header abs">
  <div class="brand abs">
    <div class="brand-mark"></div>
    <div class="brand-name">My Pebble Porch Path</div>
  </div>
  <nav class="main-nav abs">
    <span class="active">HOME</span><span>ABOUT</span><span>ADVERTISING</span><span>CONTACTS</span>
    <span class="search"><svg class="icon"><use href="#i-search"/></svg></span>
  </nav>
</header>

<section class="hero abs" role="img" aria-label="Sunset sky with a hilltop cross and a kneeling figure in silhouette"></section>
<div class="hero-title abs">My Pebble Porch Path</div>
<svg class="hero-arrow abs" style="left:30px" viewBox="0 0 30 46"><path d="M24 2L6 23l18 21"/></svg>
<svg class="hero-arrow abs" style="left:1140px" viewBox="0 0 30 46"><path d="M6 2l18 21L6 44"/></svg>

<!-- Relevant Posts -->
<section class="panel abs" style="left:97px;top:667px;width:644px;height:511px">
  <div class="panel-head"><h2 class="panel-title" style="font-weight:400">Relevant Posts</h2><div class="pager"><i></i><i class="next"></i></div></div>
  <div class="photo abs" style="left:30px;top:79px;width:584px;height:215px;background:linear-gradient(90deg,#1e1a17,#4a4038 55%,#2a2420)" role="img" aria-label="Lantern and prayer beads on a dark wooden table"></div>
  <div class="post-name abs" style="left:30px;top:318px">Rowan Ellery</div>
  <div class="meta abs" style="left:30px;top:347px">
    <span><svg class="icon"><use href="#i-cal"/></svg>17 Jan 2015</span>
    <span><svg class="icon"><use href="#i-pen"/></svg>Admin</span>
    <span><svg class="icon"><use href="#i-chat"/></svg>253 Commend</span>
  </div>
  <p class="body-copy abs" style="left:30px;top:375px;width:580px">The standard chunk of Lorem Ipsum used since the 1500s is reproduced below for those interested. Sections 1.10.32 and 1.10.33 from "de Finibus Bonorum et Malorum" by Marcus Avelin are also reproduced in their exact original form, accompanied by English versions</p>
  <div class="share-bar"><span><i></i></span><span><svg class="icon"><use href="#i-mail"/></svg></span><span><i></i></span><span><i></i></span><span class="read">Read More</span></div>
</section>

<!-- Archive Posts -->
<section class="panel abs" style="left:97px;top:1228px;width:644px;height:532px">
  <div class="panel-head"><h2 class="panel-title" style="font-weight:400;padding-left:10px">Archive Posts</h2><div class="pager"><i></i><i class="next"></i></div></div>
  <div class="abs" style="left:15px;top:82px;width:292px;height:375px;background:var(--tile)"></div>
  <div class="photo abs" style="left:15px;top:82px;width:292px;height:153px;background:linear-gradient(180deg,#c98f3e,#e8b860 45%,#6b5a34)" role="img" aria-label="Person with raised arms on a grassy dune at sunrise"></div>
  <div class="post-name abs" style="left:33px;top:252px;width:260px;line-height:26px">Harrowmere College in Vermont, looked up one</div>
  <div class="meta abs" style="left:33px;top:316px"><span><svg class="icon"><use href="#i-cal"/></svg>02/26/15</span><span><svg class="icon"><use href="#i-clock"/></svg>9:07 AM</span></div>
  <p class="body-copy abs" style="left:33px;top:345px;width:262px">Northline Computing Corp , which ruled computing in the age of the mainframe, is targeting $40 billion in annual revenue from the cloud, big data, security and other growth areas by 2018.</p>
  <div class="arch-item abs" style="top:82px"><div class="thumb" style="background:linear-gradient(135deg,#7ea6c4,#e9e2d2)" role="img" aria-label="Open hands under soft light"></div><div class="txt">embarrassing hidden in the middle of text the Internet tend to repeat predefined<div class="meta"><span><svg class="icon"><use href="#i-cal"/></svg>02/26/15</span><span><svg class="icon"><use href="#i-clock"/></svg>4:07 AM</span></div></div></div>
  <div class="arch-item abs" style="top:179px"><div class="thumb" style="background:linear-gradient(180deg,#d7dbe0,#6d6a63)" role="img" aria-label="Figure kneeling in prayer on a pier"></div><div class="txt">There are many variations of passages of Lorem Ipsum<div class="meta"><span><svg class="icon"><use href="#i-cal"/></svg>08/26/15</span><span><svg class="icon"><use href="#i-clock"/></svg>2:05 AM</span></div></div></div>
  <div class="arch-item abs" style="top:278px"><div class="thumb" style="background:linear-gradient(180deg,#c9873a,#4b2d17)" role="img" aria-label="Tree silhouette at golden dusk"></div><div class="txt">combined with a handful of model sentence structures<div class="meta"><span><svg class="icon"><use href="#i-cal"/></svg>02/27/15</span><span><svg class="icon"><use href="#i-clock"/></svg>7:09 AM</span></div></div></div>
  <div class="arch-item abs" style="top:376px"><div class="thumb" style="background:linear-gradient(135deg,#e8f1c4,#5f9a4a)" role="img" aria-label="Person in a sunlit green meadow"></div><div class="txt">therefore always free from repetition, injected humour,<div class="meta"><span><svg class="icon"><use href="#i-cal"/></svg>02/26/15</span><span><svg class="icon"><use href="#i-clock"/></svg>9:07 AM</span></div></div></div>
  <div class="share-bar"><span><i></i></span><span><svg class="icon"><use href="#i-mail"/></svg></span><span><i></i></span><span><i></i></span><span class="read">Read More</span></div>
</section>

<!-- Newsletter -->
<aside class="panel abs" style="left:787px;top:671px;width:314px;height:213px;padding:22px 24px">
  <h3 class="panel-title" style="font-weight:400;font-size:24px">Newsletter sign up</h3>
  <p style="font-size:11px;line-height:19px;margin:6px 0 12px">looked up one of the more obscure Latin words, consectetur, from a Lorem Ipsum passage,</p>
  <div class="input">Enter Your Mail</div>
  <div class="btn-dark" style="margin-top:7px">Subscribe</div>
</aside>

<!-- Recent Posts -->
<aside class="panel abs" style="left:787px;top:931px;width:314px;height:393px">
  <div class="panel-head" style="border:none;padding:0 22px 0 28px"><h3 class="panel-title" style="font-weight:400">Recent Posts</h3><div class="pager"><i></i><i class="next"></i></div></div>
  <div style="padding:6px 14px 0 28px">
    <div class="recent"><div class="thumb" style="background:linear-gradient(135deg,#c9a585,#f0ece4)" role="img" aria-label="Woman reading a book"></div><div><div class="who">Kara Whitfield</div><div class="meta"><span><svg class="icon"><use href="#i-cal"/></svg>15 Jun 2015</span><span><svg class="icon"><use href="#i-chat"/></svg>2583</span></div><div class="blurb">Tessaly Operating Results Strong, But Adverse Arbitration Award</div></div></div>
    <div class="recent"><div class="thumb" style="background:linear-gradient(135deg,#f3c98a,#5b3a22)" role="img" aria-label="Woman praying in warm light"></div><div><div class="who">Selma Dorne</div><div class="meta"><span><svg class="icon"><use href="#i-cal"/></svg>15 Jun 2015</span><span><svg class="icon"><use href="#i-chat"/></svg>2583</span></div><div class="blurb">Bramblecell Sales And Earnings Down, But Stock Price Up</div></div></div>
    <div class="recent"><div class="thumb" style="background:linear-gradient(135deg,#8a6a3b,#e2c27d)" role="img" aria-label="Open bible in golden light"></div><div><div class="who">Piers Galloway</div><div class="meta"><span><svg class="icon"><use href="#i-cal"/></svg>15 Jun 2015</span><span><svg class="icon"><use href="#i-chat"/></svg>2583</span></div><div class="blurb">Maybe Pellworth's Offer Won't Be The Last?</div></div></div>
  </div>
</aside>

<!-- Our Blogs -->
<aside class="panel abs" style="left:787px;top:1370px;width:314px;height:390px">
  <div class="panel-head" style="border:none;padding:0 14px 0 18px"><h3 class="panel-title" style="font-weight:400">Our Blogs</h3><div class="pager"><i></i><i class="next"></i></div></div>
  <div class="photo abs" style="left:20px;top:66px;width:272px;height:131px;background:linear-gradient(135deg,#3a2a24,#c8a48c 60%,#4a3028)" role="img" aria-label="Hands clasped together in prayer"></div>
  <div class="post-name abs" style="left:24px;top:218px;font-size:16px">Variations of passages</div>
  <div class="meta abs" style="left:24px;top:257px;gap:18px"><span><svg class="icon"><use href="#i-cal"/></svg>17 Jan 2015</span><span><svg class="icon"><use href="#i-pen"/></svg>Admin</span><span><svg class="icon"><use href="#i-chat"/></svg>253 Commend</span></div>
  <p class="abs" style="left:24px;top:283px;width:270px;font-size:11.5px;line-height:21px">There are many variations of passages of Lorem Ipsum available, but the majority have suffered alteration in some form</p>
  <div class="abs" style="left:24px;top:352px;font-family:'Abel',sans-serif;font-size:12px;color:#d0d0d0">Read More »</div>
</aside>

<!-- About -->
<section class="about-band abs"></section>
<h2 class="about-title abs" style="font-weight:400">Finibus Bonorum et Malorum</h2>
<div class="about-copy abs">
  <p>It is a long established fact that a reader will be distracted by the readable content of a page when looking at its layout. The point of using Lorem Ipsum is that it has a more-or-less normal distribution of letters, as opposed to using 'Content here, content here'.</p>
  <p>There are many variations of passages of Lorem Ipsum available, but the majority have suffered alteration in some form, by injected humour, or randomised words which don't look even slightly believable. If you are going to use a passage of Lorem Ipsum, you need to be sure there isn't anything embarrassing hidden in the middle of text.</p>
</div>
<div class="cart-btn abs">E-Cart <svg class="icon" style="width:18px;height:18px"><use href="#i-cart"/></svg></div>
<div class="photo abs" style="left:731px;top:1901px;width:370px;height:299px;background:linear-gradient(180deg,#6fa8e0 0%,#cfe6f7 35%,#b9d98a 58%,#4f9a2e 100%)" role="img" aria-label="Family walking across a green field toward a glowing cross in the sky"></div>

<!-- Footer -->
<footer class="site-footer abs"></footer>
<div class="social abs"><i></i><i></i><i></i><i></i></div>
<nav class="foot-nav abs"><span class="active">HOME</span><span>ABOUT</span><span>ADVERTISING</span><span>CONTACTS</span></nav>
<div class="copyright abs">Copyrights@2015&nbsp; My Pebble Porch Path</div>

</body>
</html>
```